KBT Business Cards

We require business cards for our business. We would like a matte black back to the card, with our logo centred in the middle. The front side of the card is open to design.

Target Market(s)

Clients looking for legal services (professional)

Industry/Entity Type

Legal

Contact Information for Business Card

Doran Kelbrath
Partner
Mobile: 0461 738 524
Email: doran@kbtlaw.co
Website: www.kbtlaw.co
Level 3, 118 Wendmore Street
Sydney NSW 2000

Font styles to use
Other font styles liked:
• Avenir

Colors
f04a50
ffffff
1b1b1b

Requirements
Must have
• Black back with logo included in the centre of the card.
• Our font is Avenir.

```html
<!DOCTYPE html>
<html lang="en">
<head>
<meta charset="utf-8">
<title>KBT Business Card</title>
<link rel="stylesheet" href="https://fonts.googleapis.com/css2?family=Nunito+Sans:wght@400;600;800&display=swap">
<style>
  :root {
    --brand-red: #f04a50;
    --ink: #1b1b1b;
    --paper: #ffffff;
    --stage: #e4e7eb;
    --muted: #8c8c8c;
  }
  * { margin: 0; padding: 0; box-sizing: border-box; }
  html, body { width: 1200px; height: 900px; overflow: hidden; }
  body {
    background: var(--stage);
    font-family: "Nunito Sans", "Avenir", sans-serif;
    color: var(--ink);
    position: relative;
  }
  .business-card {
    position: absolute;
    left: 150px; top: 193px;
    width: 900px; height: 512px;
    background: var(--paper);
    box-shadow: 0 18px 40px rgba(0,0,0,0.16);
    overflow: hidden;
  }
  .brand {
    position: absolute;
    left: 70px; top: 178px;
    display: flex; align-items: center; gap: 28px;
  }
  .brand-mark {
    width: 96px; height: 96px;
    background: var(--brand-red);
  }
  .brand-name {
    font-size: 30px; font-weight: 600; line-height: 1.08;
    color: var(--ink); text-transform: uppercase; letter-spacing: 0.2px;
  }
  .divider {
    position: absolute;
    left: 488px; top: 170px;
    width: 2px; height: 166px;
    background: var(--ink);
  }
  .contact-block {
    position: absolute;
    left: 527px; top: 170px;
  }
  .person-name {
    font-size: 29px; font-weight: 800; letter-spacing: 0.6px;
    text-transform: uppercase; line-height: 1;
  }
  .person-name .surname { color: var(--brand-red); }
  .person-role {
    font-size: 19px; font-weight: 400; margin-top: 10px;
  }
  .contact-list { list-style: none; margin-top: 26px; }
  .contact-list li {
    display: flex; align-items: center; gap: 12px;
    font-size: 20px; line-height: 28px; letter-spacing: 0.3px;
  }
  .contact-list svg { width: 16px; height: 16px; fill: var(--brand-red); flex: none; }
  .address-band {
    position: absolute;
    left: 0; bottom: 0;
    width: 100%; height: 68px;
    background: var(--ink);
    border-top: 3px solid var(--brand-red);
    display: flex; align-items: center; justify-content: center;
    font-size: 20px; color: var(--muted); letter-spacing: 0.4px;
  }
</style>
</head>
<body>
  <div class="business-card">
    <div class="brand">
      <div class="brand-mark"></div>
      <div class="brand-name">Kelbrath<br>Bryce<br>Legal</div>
    </div>

    <div class="divider"></div>

    <div class="contact-block">
      <h1 class="person-name">Doran <span class="surname">Kelbrath</span></h1>
      <p class="person-role">Partner</p>
      <ul class="contact-list">
        <li>
          <svg viewBox="0 0 24 24" aria-hidden="true"><path d="M6.6 10.8c1.4 2.8 3.8 5.1 6.6 6.6l2.2-2.2c.3-.3.7-.4 1-.2 1.1.4 2.3.6 3.6.6.6 0 1 .4 1 1V20c0 .6-.4 1-1 1C10.6 21 3 13.4 3 4c0-.6.4-1 1-1h3.5c.6 0 1 .4 1 1 0 1.3.2 2.5.6 3.6.1.3 0 .7-.2 1z"/></svg>
          0461 738 524
        </li>
        <li>
          <svg viewBox="0 0 24 24" aria-hidden="true"><path d="M2 5h20v14H2z" opacity=".85"/><path d="M2 5l10 8 10-8" fill="none" stroke="#fff" stroke-width="2"/></svg>
          doran@kbtlaw.co
        </li>
        <li>
          <svg viewBox="0 0 24 24" aria-hidden="true"><circle cx="12" cy="12" r="10"/><path d="M2 12h20M12 2c3 3 3 17 0 20M12 2c-3 3-3 17 0 20" fill="none" stroke="#fff" stroke-width="1.5"/></svg>
          www.kbtlaw.co
        </li>
      </ul>
    </div>

    <div class="address-band">Level 3, 118 Wendmore Street, Sydney NSW 2000</div>
  </div>
</body>
</html>
```